business card design for a plumbing contractor

i need a double business card for a plumbing business, our initial service is residential Sewer Drain Cleaning.

Target Market(s)

other plumbing Business

Industry/Entity Type

Plumbing

Contact Information for Business Card

www.PipeworksTopMark.example- 5307218394-

Font styles to use
Serif

Colors
ec1f27
0455a3

```html
<!DOCTYPE html>
<html lang="en">
<head>
<meta charset="utf-8">
<title>Pipeworks Top Mark – Business Card</title>
<link href="https://fonts.googleapis.com/css2?family=Roboto+Condensed:wght@400;700&display=swap" rel="stylesheet">
<style>
  :root {
    --red: #d9372f;
    --white: #ffffff;
    --paper: #f4f4f4;
    --grey-text: #5a5a5a;
    --logo-grey: #8a8580;
    --stage: #e6e3de;
  }
  * { box-sizing: border-box; margin: 0; padding: 0; }
  html, body { width: 1200px; height: 886px; overflow: hidden; }
  body {
    background: var(--stage);
    font-family: "Roboto Condensed", Arial, sans-serif;
    position: relative;
  }
  .card {
    position: absolute;
    top: 300px;
    width: 500px;
    height: 286px;
    border-radius: 18px;
    overflow: hidden;
    box-shadow: 0 6px 18px rgba(0,0,0,0.18);
  }
  .card--front { left: 70px; background: var(--white); }
  .card--back { left: 630px; background: var(--paper); display: flex; align-items: center; justify-content: center; }

  .front__panel {
    position: absolute; left: 0; top: 0; right: 0; height: 246px;
    background: var(--red);
    color: var(--white);
    display: flex; align-items: center; justify-content: center;
  }
  .identity { text-align: right; padding-right: 18px; }
  .identity__name { font-weight: 700; font-size: 21px; letter-spacing: 0.5px; }
  .identity__title { font-size: 15px; letter-spacing: 0.5px; margin-top: 2px; }
  .divider { width: 1px; height: 64px; background: rgba(255,255,255,0.6); }
  .contacts { list-style: none; padding-left: 18px; font-size: 13px; }
  .contacts li { display: flex; align-items: center; gap: 8px; line-height: 20px; }
  .contacts svg { width: 11px; height: 11px; flex: none; }

  .front__services {
    position: absolute; left: 0; right: 0; bottom: 0; height: 40px;
    display: flex; align-items: center; justify-content: center; gap: 8px;
    font-size: 14px; color: var(--grey-text);
  }
  .services__dot { width: 5px; height: 5px; border-radius: 50%; background: var(--red); }

  .brand { display: flex; align-items: center; gap: 14px; }
  .brand__mark { width: 26px; height: 26px; background: var(--red); }
  .brand__name { font-weight: 700; font-size: 40px; color: var(--logo-grey); letter-spacing: 0.5px; }
</style>
</head>
<body>
  <section class="card card--front" aria-label="Card front">
    <div class="front__panel">
      <div class="identity">
        <p class="identity__name">ALEX MORGAN</p>
        <p class="identity__title">CEO/FOUNDER</p>
      </div>
      <div class="divider"></div>
      <ul class="contacts">
        <li>
          <svg viewBox="0 0 12 12" aria-hidden="true"><path fill="#fff" d="M2.5 1l2 2-1 1.5c.7 1.5 1.8 2.6 3.3 3.3L8.3 6.8l2 2L9 10.8C5 10.3 1.7 7 1.2 3z"/></svg>
          5307218394
        </li>
        <li>
          <svg viewBox="0 0 12 12" aria-hidden="true"><rect x="1" y="2.5" width="10" height="7" fill="#fff"/><path d="M1 2.5l5 4 5-4" stroke="#d9372f" fill="none"/></svg>
          Dispatch@PipeworksTopMark.example
        </li>
        <li>
          <svg viewBox="0 0 12 12" aria-hidden="true"><circle cx="6" cy="6" r="5" fill="#fff"/><path d="M1 6h10M6 1c-2 2.5-2 7.5 0 10M6 1c2 2.5 2 7.5 0 10" stroke="#d9372f" stroke-width="0.8" fill="none"/></svg>
          www.PipeworksTopMark.example
        </li>
      </ul>
    </div>
    <div class="front__services">
      <span>Sewer Drain Cleaning</span><span class="services__dot"></span>
      <span>Maintenance</span><span class="services__dot"></span>
      <span>Trenchless Pipe Installs</span>
    </div>
  </section>

  <section class="card card--back" aria-label="Card back">
    <div class="brand">
      <span class="brand__mark"></span>
      <span class="brand__name">Pipeworks Top Mark</span>
    </div>
  </section>
</body>
</html>
```